Corvane Business Cards

Front of business card will have logo, name, address, & telephone number. Back of card will have a list of services provided - Roads, Substation Pads, Temporary Pads, Site Pads, Land Leveling, Powerline Row Cleaning, Land Clearing, Gates, Fencing, Construction Entrances, Excavation, Trenching, Underground Utilities, Directional Boring, Pile Driving. We are a construction company that uses heavy equipment like bulldozers, motor graders/blades, dump trucks, backhoes, hydro axes, & skid loaders. We build roads, pads, & install electric utility lines & waterlines underground. This logo is new. The word "Construction" can be smaller as uploaded 2 example edited logos. We will be using this card design for many employees.
Target Market(s)
Industrial Electric Powerline, Wind Turbine, Solar Panel, & Water Utility companies.
Contact Information for Business Card
Name/Position - Dwayne Halster - Owner
Address: 4875 FM 309
Merkel, TX 79412
Phone number - (325) 482-5096

```html
<!DOCTYPE html>
<html lang="en">
<head>
<meta charset="utf-8">
<title>Corvane Construction Business Cards</title>
<link rel="stylesheet" href="https://fonts.googleapis.com/css2?family=Cinzel:wght@600;700&family=Roboto:wght@400;500&display=swap">
<style>
  :root {
    --maroon: #3b121b;
    --maroon-deep: #2e0d14;
    --paper: #ffffff;
    --ink: #3b121b;
    --text-dark: #2a1a1d;
    --stage: #e8eded;
    --rule: #6b5a5d;
  }
  * { box-sizing: border-box; margin: 0; padding: 0; }
  html, body { width: 1200px; height: 900px; overflow: hidden; }
  body {
    background: var(--stage);
    display: flex;
    align-items: center;
    justify-content: center;
    gap: 60px;
    font-family: "Roboto", Arial, sans-serif;
  }
  .card {
    position: relative;
    width: 520px;
    height: 297px;
    overflow: hidden;
    box-shadow: 0 10px 24px rgba(40, 20, 25, 0.18);
  }
  .card-front { background: var(--paper); }
  .card-back { background: linear-gradient(135deg, var(--maroon) 0%, var(--maroon-deep) 100%); }

  .wave { position: absolute; inset: 0; width: 100%; height: 100%; }

  .wordmark {
    position: absolute;
    font-family: "Cinzel", Georgia, serif;
    font-weight: 700;
    line-height: 1;
    display: flex;
    align-items: center;
    gap: 12px;
  }
  .wordmark .mark-square { width: 16px; height: 16px; flex: none; }
  .wordmark .name-lines { display: flex; flex-direction: column; gap: 6px; }
  .wordmark .line-main { font-size: 40px; letter-spacing: 2px; }
  .wordmark .line-sub { font-size: 21px; letter-spacing: 1.5px; }

  .card-front .wordmark { left: 46px; top: 40px; color: var(--ink); }
  .card-front .mark-square { background: var(--ink); }

  .person { position: absolute; left: 40px; top: 178px; color: var(--ink); }
  .person-name { font-family: "Cinzel", Georgia, serif; font-weight: 700; font-size: 19px; letter-spacing: 1px; }
  .person-role { font-size: 12px; color: var(--text-dark); text-align: right; margin-top: 2px; }

  .divider { position: absolute; left: 262px; top: 128px; width: 1px; height: 66px; background: var(--rule); }

  .contact { position: absolute; left: 278px; top: 128px; font-size: 14px; line-height: 21px; color: var(--text-dark); letter-spacing: 0.5px; font-style: normal; }
  .contact .phone { display: flex; align-items: center; gap: 6px; }
  .contact svg { width: 13px; height: 13px; fill: var(--ink); }

  .services { position: absolute; left: 30px; top: 28px; list-style: none; color: var(--paper); font-size: 12.5px; letter-spacing: 0.4px; }
  .services li { display: flex; align-items: center; gap: 9px; height: 16px; }
  .services li::before { content: ""; width: 6px; height: 6px; border-radius: 50%; background: var(--paper); flex: none; }

  .card-back .wordmark { left: 232px; top: 112px; color: var(--paper); }
  .card-back .mark-square { background: var(--paper); }
  .card-back .line-main { font-size: 38px; }
  .card-back .line-sub { font-size: 20px; }
</style>
</head>
<body>
  <section class="card card-front" aria-label="Business card front">
    <svg class="wave" viewBox="0 0 520 297" preserveAspectRatio="none" aria-hidden="true">
      <path fill="var(--maroon)" d="M0,297 L0,290 C40,288 70,268 110,264 C150,260 175,266 210,252 C245,238 265,226 305,222 C345,218 360,224 395,212 C430,200 450,206 480,196 C500,190 510,192 520,186 L520,297 Z"/>
    </svg>
    <div class="wordmark">
      <span class="mark-square"></span>
      <span class="name-lines"><span class="line-main">CORVANE</span><span class="line-sub">CONSTRUCTION</span></span>
    </div>
    <div class="person">
      <div class="person-name">DWAYNE HALSTER</div>
      <div class="person-role">Owner</div>
    </div>
    <span class="divider"></span>
    <address class="contact">
      <div>4875 FM 309, Calvera</div>
      <div>TX 79412</div>
      <div class="phone"><svg viewBox="0 0 24 24" aria-hidden="true"><path d="M6.6 10.8c1.4 2.8 3.8 5.1 6.6 6.6l2.2-2.2c.3-.3.7-.4 1-.2 1.1.4 2.3.6 3.6.6.6 0 1 .4 1 1V20c0 .6-.4 1-1 1C10.6 21 3 13.4 3 4c0-.6.4-1 1-1h3.5c.6 0 1 .4 1 1 0 1.3.2 2.5.6 3.6.1.3 0 .7-.2 1L6.6 10.8z"/></svg>(325) 482-5096</div>
    </address>
  </section>

  <section class="card card-back" aria-label="Business card back">
    <ul class="services">
      <li>Roads</li>
      <li>Substation Pads</li>
      <li>Temporary Pads</li>
      <li>Site Pads</li>
      <li>Land Leveling</li>
      <li>Powerline Row Cleaning</li>
      <li>Land Clearing</li>
      <li>Gates</li>
      <li>Fencing</li>
      <li>Construction Entrances</li>
      <li>Excavation</li>
      <li>Trenching</li>
      <li>Underground Utilities</li>
      <li>Directional Boring</li>
      <li>Pile Driving</li>
    </ul>
    <div class="wordmark">
      <span class="mark-square"></span>
      <span class="name-lines"><span class="line-main">CORVANE</span><span class="line-sub">CONSTRUCTION</span></span>
    </div>
  </section>
</body>
</html>
```